Website development company website

ABOUT COMPANY
Hi everyone! We're a Melbourne, Australia website development company in a need of a website design that will make online store merchants want to engage our services.
We specialise exclusively in Torvista e-commerce platform (https://torvista-platform.example/). What distinguishes our business from competition is that rather than designing and building brand new websites, we offer development, support and maintenance services to established websites. Maintenance and Support are the keywords representing our business.
Our potential clients are people with broken, slow and underperforming Torvista installations who need assistance getting their websites up and making sales. Our website must pass the message that we can help, and provide quick means of making contact.
DESIGN
Overall, we're looking for a slick, clean, airy, conservative design. No need to do anything crazy, try to stick to what's "standard" in website design these days and make it easy on all of us. The website is unlikely to be updated too often so it needs to look attractive and fresh first time over and after a year, too.
Attached is our new logo, which you'll be able to take the basic idea from, the colors and fonts. Though, don't use the fonts from the logo in the website, stick to the standard widely supported fonts. Additional use of Google fonts is fine.
Don't overdo it with colors, stick to conservative basic color set and only use the colors from the log for accents like headings etc. Please, don't be tempted to use the blue and orange as background of whole blocks, other than perhaps footer. Thanks.
For the images used, I'd like to stay away from a design studio/digital agency feel and lean more towards professional support and maintenance services. I'm thinking images of content merchants doing their job. Something along the lines of "We'll be taking care of the website so that you only need to care about the business".
Some ideas I like:
http://www.plumframe-pics.example/detail/photo/portrait-of-confident-male-design-professional-royalty-free-image/572048163
http://www.plumframe-pics.example/detail/photo/designer-taking-picture-of-hat-high-res-stock-photography/839207514
http://www.plumframe-pics.example/detail/photo/woman-packaging-pottery-royalty-free-image/216684093
Images of colorful shopping bags and shopping carts are over the top and not serious enough. Instead of images matching Online Shopping, I'd try going more for Stability, Reliability, Performance.
Our existing website is http://www.bravuln.example. Please, don't take design ideas from it, but it will give you a picture of the structure of our new website and content that's going to be used initially.
If you could include a basic icon set to use throughout the website, that would be great. If the icons could match our logo (attached), it would be a big plus.
ALL PAGES
Every page must contain clearly visible phone number (1300 648 907) and a Contact Us Now button, which opens an AJAX driven popup form with Name, Email, Phone and Message to be sent through.
To start with, main menu items will be Torvista, Portfolio, Contact.
At the bottom of each page, please, include a newsletter subscription form with text Subscribe to Torvista Support and Security Updates.
For the footer, I'd like to see a logo strip with the following logos in grayscale (no need to link anywhere): Torvista, QRX, DataVane, NCB. You'll find the logos on Google Images.
Standard footer columns follow. Here, I'd like to see logos in color: Torvista Certified Developer, Torvista Ceritified Solution Provider. Again, the logos are on Google Images.
No social media logos/links necessary anywhere on the website.
...and then the copyright line.
FRONT PAGE
Large slider with images that would appeal to our target audience. Keywords here would be Torvista System Audit, Torvista Performance Optimisation, Torvista Website Emergency Recovery, Torvista Development Infrastructure Hosting. We'll have a static page created for each of these to link to.
In a corner of the slider, or on the edge, can I have an overlay with logos in color (same as footer): Torvista Certified Developer, Torvista Ceritified Solution Provider.
Underneath, a number of blocks, each with an image and teaser that we'll use to link to various pages throughout the website.
PORTFOLIO PAGE
I'm thinking a single long page with a block per client, which will contain project name, description from us and a testimonial from client. Also, each block will contain a single large screenshot. No gallery or slideshow is necessary here, just one image per project.
I'll leave the layout up to you, but try to put yourself in the shoes of a potential client reviewing our past work by simply scrolling down this one page.
CONTACT US PAGE
Separate page with the same form as above, phone number (1300 648 907), email address (support@kavreo.example), address (Suite 42, Level 3|8 Wattlebrook Lane|Fernvale Heights VIC 3999), and a grayscale Google Map.
CODING UP
Coding up into static HTML/CSS/JS is equally important as the design itself. We're a website development company, we'll be integrating the theme. We will spot any issues and we will point them out.
Coded up design must be fully responsive. Enough said.
To be able to create any content in future, we'd like one extra page coded up with samples of all themed elements, lists, forms, buttons, 2, 3, 4-column layout, alerts, icons, etc. This page does not need to be designed, only coded up.
The design will be integrated into Drupal using Twig. If possible at all, try to keep it in mind when designing and coding up, and make the integration into a Drupal theme easier for us.
GOOD LUCK!
That's it. Let me know if anything needs clarifying. So far I've had a great experience with ArtFlockly. I don't doubt some great designs will emerge. Clever ideas are highly appreciated, but also make it clear you've read and followed the points in this brief. Cheers, Tom

```html
<!DOCTYPE html>
<html lang="en">
<head>
<meta charset="utf-8">
<title>Kavreo Commerce – Torvista Development &amp; Support</title>
<link href="https://fonts.googleapis.com/css2?family=Open+Sans:ital,wght@0,400;0,600;0,700;1,400;1,600&display=swap" rel="stylesheet">
<style>
:root{
  --orange:#e2761f;
  --orange-dark:#c9631a;
  --blue:#1f5592;
  --ink:#333638;
  --muted:#7a7d80;
  --line:#dcdcdc;
  --footer:#2b2b2d;
  --footer-deep:#1d1d1f;
  --white:#ffffff;
}
*{box-sizing:border-box;margin:0;padding:0}
html,body{width:1200px;height:2341px;overflow:hidden}
body{font-family:"Open Sans",Arial,sans-serif;color:var(--ink);background:var(--white);position:relative}
a{color:inherit;text-decoration:none}
.abs{position:absolute}

/* Hero */
.hero{position:absolute;left:0;top:0;width:1200px;height:604px;overflow:hidden}
.hero-media{position:absolute;inset:0;
  background:
    radial-gradient(ellipse 320px 220px at 880px 420px, rgba(214,140,60,.55), transparent 70%),
    radial-gradient(ellipse 260px 160px at 1080px 360px, rgba(200,120,50,.45), transparent 70%),
    radial-gradient(ellipse 300px 260px at 380px 330px, #cfd3d8 0%, #9aa0a8 45%, transparent 75%),
    linear-gradient(180deg,#101214 0%,#1a1c1f 55%,#2b2218 100%)}
.site-header{position:absolute;left:0;top:0;width:1200px;height:140px}
.brand{position:absolute;left:98px;top:44px;display:flex;align-items:center;gap:12px}
.brand-square{width:30px;height:30px;background:var(--orange)}
.brand-name{font-size:30px;font-weight:700;color:var(--white);letter-spacing:-.5px}
.contact-line{position:absolute;right:98px;top:32px;display:flex;gap:32px;font-size:12.5px;color:var(--white)}
.contact-line span{display:flex;align-items:center;gap:8px}
.contact-line small{font-size:10px;font-weight:600}
.main-nav{position:absolute;right:160px;top:85px;display:flex;gap:58px;font-size:11px;font-weight:600;color:var(--white)}
.main-nav .is-current{color:var(--orange)}
.search-btn{position:absolute;left:1066px;top:77px;width:34px;height:34px;border-radius:50%;background:#6b3a12;display:flex;align-items:center;justify-content:center}
.slide-caption{position:absolute;right:98px;top:240px;text-align:right;color:var(--white)}
.slide-kicker{font-size:20px;font-weight:600;letter-spacing:.5px}
.slide-title{font-size:44px;font-weight:700;letter-spacing:1px;line-height:1.25}
.btn{display:inline-flex;align-items:center;justify-content:center;background:var(--orange);color:var(--white);font-size:12.5px;font-weight:600;text-transform:uppercase;border-radius:3px}
.slide-btn{position:absolute;left:975px;top:342px;width:125px;height:45px;border:2px solid var(--white);border-radius:4px}
.cert-badges{position:absolute;left:957px;top:459px;display:flex;gap:11px}
.cert-badge{width:66px;height:103px;border:1px solid rgba(255,255,255,.8);display:flex;align-items:center;justify-content:center}
.cert-badge i{display:block;width:38px;height:72px;background:linear-gradient(180deg,var(--orange) 0 55%,#9b9b9b 55%)}
.cert-badge.alt i{background:linear-gradient(180deg,#c8c8c8 0 55%,#8a8a8a 55%)}
.slider-dots{position:absolute;left:852px;top:548px;display:flex;gap:10px}
.slider-dots span{width:16px;height:16px;border-radius:50%;background:var(--white)}
.slider-dots .is-active{background:transparent;border:2px solid var(--orange);position:relative}
.slider-dots .is-active::after{content:"";position:absolute;left:3px;top:3px;width:6px;height:6px;border-radius:50%;background:var(--orange)}

/* Section headings */
.section-title{position:absolute;left:0;width:1200px;display:flex;justify-content:center;align-items:center;gap:12px;font-size:23px;font-weight:600;color:var(--ink);text-transform:uppercase}
.title-mark{width:18px;height:22px;background:var(--blue);border-top:5px solid var(--orange)}
.section-lead{position:absolute;left:168px;width:865px;text-align:center;font-size:12.5px;line-height:26px;color:var(--muted)}

/* Feature cards */
.feature{position:absolute;top:866px;width:312px;height:284px;border:1px solid var(--line);text-align:center}
.feature-icon{position:absolute;left:92px;top:-59px;width:128px;height:128px;border-radius:50%;border:2px solid var(--orange);background:var(--white);display:flex;align-items:center;justify-content:center}
.feature-title{position:absolute;top:100px;width:100%;font-size:13px;font-weight:600;color:var(--orange);text-transform:uppercase}
.feature-text{position:absolute;top:128px;left:22px;right:22px;font-size:12px;line-height:22px;color:var(--muted)}
.feature .btn{position:absolute;left:94px;top:207px;width:123px;height:43px}

.divider{position:absolute;left:98px;top:1195px;width:1002px;height:1px;background:var(--line)}

/* Work */
.work-item{position:absolute;top:1340px;width:248px;text-align:center}
.work-media{height:167px}
.work-title{margin-top:17px;font-size:14px;font-weight:600;line-height:22px;color:var(--ink);text-transform:uppercase}
.work-link{display:block;margin-top:4px;font-size:10.5px;font-style:italic;color:var(--orange)}
.work-item.is-hover .work-media{height:167px;margin-top:0}
.work-item.is-hover .work-title{margin-top:2px;padding:12px 0 6px;background:#1f1f1f;color:#4a4a4a;margin-left:0;width:248px}

/* Testimonials */
.testimonials{position:absolute;left:0;top:1628px;width:1200px;height:288px;
  background:radial-gradient(ellipse 260px 200px at 430px 120px, rgba(120,150,190,.55), transparent 70%),linear-gradient(90deg,#1b4a82 0%,#25599a 50%,#1d4c86 100%);color:var(--white)}
.testimonials .section-title{top:76px;color:var(--white)}
.testimonials .title-mark{background:var(--white);border-top-color:var(--white)}
.quote{position:absolute;top:138px;width:1200px;text-align:center;font-size:13px;font-style:italic;line-height:25px}
.quote .mark{font-size:26px;font-style:normal;vertical-align:-6px}
.arrow{position:absolute;top:166px}

/* Tech strip */
.tech-strip{position:absolute;left:0;top:1916px;width:1200px;height:120px;border-bottom:3px solid var(--orange);display:flex}
.tech-cell{height:100%;display:flex;align-items:center;justify-content:center;font-size:32px;font-weight:600;color:#555;border-right:1px solid var(--line)}
.tech-cell:last-child{border-right:0}

/* Footer */
.site-footer{position:absolute;left:0;top:2039px;width:1200px;height:229px;background:var(--footer);color:#9a9a9a}
.footer-brand{position:absolute;left:98px;top:70px;display:flex;align-items:center;gap:10px}
.footer-brand .brand-square{background:#6d6d6d;width:28px;height:28px}
.footer-brand .brand-name{color:#8a8a8a;font-size:28px}
.footer-about{position:absolute;left:98px;top:128px;width:225px;font-size:12px;line-height:24px}
.footer-col h4{position:absolute;top:36px;font-size:14px;font-weight:600;color:var(--white);text-transform:uppercase}
.footer-list{position:absolute;top:72px;list-style:none;font-size:11px;text-transform:uppercase}
.footer-list li{height:26px;display:flex;align-items:flex-start;gap:8px}
.contact-list li{height:auto;margin-bottom:12px;line-height:20px}
.footer-map{position:absolute;left:783px;top:40px;width:317px;height:147px;border:2px solid #d0d0d0;background:linear-gradient(135deg,#e9e9e9,#cfcfcf)}
.bottom-bar{position:absolute;left:0;top:2268px;width:1200px;height:73px;background:var(--footer-deep);color:var(--white);font-size:11px;font-weight:600}
.copyright{position:absolute;left:98px;top:28px}
.support{position:absolute;right:98px;top:14px;display:flex;align-items:center;gap:8px}
.support i{display:block;width:22px;height:44px;border:1px solid #ccc;background:linear-gradient(180deg,var(--orange) 0 55%,#999 55%)}
</style>
</head>
<body>

<header class="hero">
  <div class="hero-media" role="img" aria-label="Hands typing on a laptop showing an online store, city skyline at night behind"></div>
  <div class="site-header">
    <a class="brand" href="#"><span class="brand-square"></span><span class="brand-name">Kavreo</span></a>
    <div class="contact-line">
      <span><svg width="18" height="18" viewBox="0 0 24 24" fill="none" stroke="#fff" stroke-width="1.8"><path d="M5 3h4l2 5-3 2a12 12 0 0 0 6 6l2-3 5 2v4a2 2 0 0 1-2 2A17 17 0 0 1 3 5a2 2 0 0 1 2-2z"/></svg><small>PHONE:</small> 1300 648 907</span>
      <span><svg width="20" height="16" viewBox="0 0 24 18" fill="none" stroke="#fff" stroke-width="1.6"><rect x="1" y="1" width="22" height="16"/><path d="M1 1l11 9 11-9"/></svg><small>MAIL:</small> support@kavreo.example</span>
    </div>
    <nav class="main-nav">
      <a class="is-current" href="#">HOME</a><a href="#">ABOUT US</a><a href="#">PORTFOLIO</a><a href="#">CONTACT US</a>
    </nav>
    <a class="search-btn" href="#"><svg width="12" height="12" viewBox="0 0 24 24" fill="none" stroke="#fff" stroke-width="3"><circle cx="10" cy="10" r="7"/><path d="M15 15l7 7"/></svg></a>
  </div>
  <div class="slide-caption">
    <p class="slide-kicker">TORVISTA DEVELOPMENT</p>
    <h1 class="slide-title">INFRASTRUCTURE</h1>
  </div>
  <a class="btn slide-btn" href="#">Read More</a>
  <div class="cert-badges">
    <div class="cert-badge"><i></i></div>
    <div class="cert-badge alt"><i></i></div>
  </div>
  <div class="slider-dots"><span class="is-active"></span><span></span><span></span></div>
</header>

<main>
  <h2 class="section-title" style="top:651px"><span class="title-mark"></span>Welcome to Bravuln</h2>
  <p class="section-lead" style="top:702px">Sed ut perspiciatis unde omnis iste natus error sit voluptatem accusantium doloremque laudantium, totam rem aperiam, eaque ipsa quae ab illo inventore veritatis et quasi architecto beatae vitae dicta sunt explicabo. Nemo enim ipsam voluptatem quia voluptas sit aspernatur aut odit aut fugit, sed quia consequuntur magni dolores eos qui ratione voluptatem sequi nesciunt...</p>

  <article class="feature" style="left:98px">
    <div class="feature-icon"><svg width="50" height="50" viewBox="0 0 24 24" fill="var(--orange)"><path d="M2 3h8l10 10-8 8L2 11z"/><circle cx="6.5" cy="7.5" r="1.6" fill="#fff"/><path d="M13 3h2l9 10-8 8-1-1 7-7z"/></svg></div>
    <h3 class="feature-title">Why Bravuln?</h3>
    <p class="feature-text">Fast Torvista-based online stores, built on time and to specification, backed by effective, focused support, means that our clients...</p>
    <a class="btn" href="#">Read More</a>
  </article>
  <article class="feature" style="left:445px">
    <div class="feature-icon"><svg width="52" height="46" viewBox="0 0 26 22" fill="none" stroke="var(--orange)" stroke-width="2"><rect x="1" y="1" width="24" height="20"/><circle cx="8" cy="7" r="2" fill="var(--orange)"/><path d="M3 19l7-7 4 4 4-5 6 8" fill="var(--orange)"/></svg></div>
    <h3 class="feature-title">Why Torvista?</h3>
    <p class="feature-text">Torvista is the world's leading open source eCommerce platform. No other open-source or free system offers...</p>
    <a class="btn" href="#">Read More</a>
  </article>
  <article class="feature" style="left:788px">
    <div class="feature-icon"><svg width="54" height="40" viewBox="0 0 28 20" fill="none" stroke="var(--orange)" stroke-width="2"><rect x="5" y="1" width="18" height="14" rx="1"/><path d="M1 18h26"/></svg></div>
    <h3 class="feature-title">What We Do</h3>
    <p class="feature-text">From support, maintenance and upgrades to redesigns, migrations and full site builds, we make your online...</p>
    <a class="btn" href="#">Read More</a>
  </article>

  <div class="divider"></div>

  <h2 class="section-title" style="top:1239px"><span class="title-mark"></span>Our Work</h2>
  <p class="section-lead" style="top:1285px">Veritatis et quasi architecto beatae vitae dicta sunt explicabo. Nemo enim ipsam voluptatem quia voluptas sit aspernatur</p>

  <article class="work-item" style="left:98px">
    <div class="work-media" role="img" aria-label="Person at a desk reviewing code on a monitor" style="background:linear-gradient(135deg,#3a4a5a,#c9d3dc 60%,#eef1f3)"></div>
    <h3 class="work-title">Torvista System<br>Audit</h3>
    <a class="work-link" href="#">Click View More Information</a>
  </article>
  <article class="work-item is-hover" style="left:350px">
    <div class="work-media" role="img" aria-label="Hands on a desk with printed performance charts" style="background:linear-gradient(180deg,#fff 0 20%,#e6e0da 20%,#c7b8a8 100%)"></div>
    <h3 class="work-title">Torvista Performance<br>Optimisation</h3>
    <a class="work-link" href="#">Click View More Information</a>
  </article>
  <article class="work-item" style="left:601px">
    <div class="work-media" role="img" aria-label="Businessman touching an internal control screen" style="background:linear-gradient(135deg,#0e3a66,#2f7bc0 55%,#9cc8ea)"></div>
    <h3 class="work-title">Website<br>Emergency Recovery</h3>
    <a class="work-link" href="#">Click View More Information</a>
  </article>
  <article class="work-item" style="left:853px">
    <div class="work-media" role="img" aria-label="Several devices showing website layouts" style="background:linear-gradient(135deg,#f4f6f8,#c9d2da 60%,#7a8a99)"></div>
    <h3 class="work-title">Torvista Development<br>Infrastructure Hosting</h3>
    <a class="work-link" href="#">Click View More Information</a>
  </article>

  <section class="testimonials" role="img" aria-label="Smiling customer holding a card, tinted blue">
    <h2 class="section-title"><span class="title-mark"></span>Testimonials</h2>
    <blockquote class="quote">
      Lacewell Co-Glimmera Pelko<br>
      <span class="mark">&ldquo;</span>A fast solution is key when you are selling online. Bravuln are now our go to Torvista developers, very happy<span class="mark">&rdquo;</span><br>
      -Ravi Oldmeadow, Pelko
    </blockquote>
    <svg class="arrow" style="left:98px" width="10" height="14" viewBox="0 0 10 14"><path d="M8 1L2 7l6 6" fill="none" stroke="#fff" stroke-width="2.5"/></svg>
    <svg class="arrow" style="left:1092px" width="10" height="14" viewBox="0 0 10 14"><path d="M2 1l6 6-6 6" fill="none" stroke="#fff" stroke-width="2.5"/></svg>
  </section>

  <div class="tech-strip">
    <div class="tech-cell" style="width:350px">Torvista</div>
    <div class="tech-cell" style="width:249px">QRX</div>
    <div class="tech-cell" style="width:251px">DataVane</div>
    <div class="tech-cell" style="width:350px">NCB</div>
  </div>
</main>

<footer class="site-footer">
  <div class="footer-brand"><span class="brand-square"></span><span class="brand-name">Kavreo</span></div>
  <p class="footer-about">sed quia consequuntur magni dolores nesciunt. Neque porro quisquam est, qui dolorem ipsum quia dolor...</p>

  <div class="footer-col">
    <h4 style="left:370px">Navigation</h4>
    <ul class="footer-list" style="left:372px">
      <li>&#8250; Home</li><li>&#8250; About Us</li><li>&#8250; Portfolio</li><li>&#8250; Contact Us</li>
    </ul>
  </div>
  <div class="footer-col">
    <h4 style="left:524px">Contact Us</h4>
    <ul class="footer-list contact-list" style="left:526px;width:230px">
      <li><svg width="10" height="14" viewBox="0 0 10 14" style="flex:none;margin-top:3px"><path d="M5 0a5 5 0 0 1 5 5c0 4-5 9-5 9S0 9 0 5a5 5 0 0 1 5-5z" fill="#8a8a8a"/><circle cx="5" cy="5" r="2" fill="#2b2b2d"/></svg><span>Suite 42, Level 3|8 Wattlebrook Lane|Fernvale Heights VIC 3999</span></li>
      <li><svg width="12" height="12" viewBox="0 0 24 24" fill="#8a8a8a" style="flex:none;margin-top:4px"><path d="M5 3h4l2 5-3 2a12 12 0 0 0 6 6l2-3 5 2v4a2 2 0 0 1-2 2A17 17 0 0 1 3 5a2 2 0 0 1 2-2z"/></svg><span>Phone: 1300 648 907</span></li>
      <li><svg width="13" height="10" viewBox="0 0 24 18" fill="none" stroke="#8a8a8a" stroke-width="2.5" style="flex:none;margin-top:5px"><rect x="1" y="1" width="22" height="16"/><path d="M1 1l11 9 11-9"/></svg><span>support@kavreo.example</span></li>
    </ul>
  </div>
  <div class="footer-map" role="img" aria-label="Grayscale street map with office location pin"></div>
</footer>

<div class="bottom-bar">
  <p class="copyright">COPYRIGHTS©BRAVULN.2016 | ALLRIGHTS RESERVED.</p>
  <div class="support">TORVISTA SUPPORT: <i></i><i style="background:linear-gradient(180deg,#ccc 0 55%,#888 55%)"></i></div>
</div>

</body>
</html>
```